Business Card Design for a Personal Trainer

I need a business card design for my job as a personal trainer. It should have a unique, modern and exclusive design. On the front there should be only my logo with my name and my job. 0162/3819204 Tobias Lendhart Wiesengrundweg 14 80417 Munich Germany The most important contact information is the web adress. it can be bigger than the rest, but its not necessary. The card should be 8,5cmx5,5cm big. Font: Roboto. Colors: black, white, gray, 56c1ff.

```html
<!DOCTYPE html>
<html lang="de">
<head>
<meta charset="utf-8">
<title>Tobias Lendhart – Personal Trainer Business Card</title>
<link href="https://fonts.googleapis.com/css2?family=Roboto:ital,wght@0,400;0,500;1,700&display=swap" rel="stylesheet">
<style>
  :root {
    --stage: #141414;
    --card-light: #2d3034;
    --card-dark: #232629;
    --white: #ffffff;
    --soft-white: #e9ecef;
    --accent: #56c1ff;
    --photo-dark: #1c1d1f;
    --photo-mid: #4a4c4f;
  }
  * { box-sizing: border-box; margin: 0; padding: 0; }
  html, body {
    width: 1189px; height: 1200px; overflow: hidden;
    background: var(--stage);
    font-family: "Roboto", Arial, sans-serif;
  }
  .card {
    position: absolute; left: 219px;
    width: 752px; height: 487px;
    overflow: hidden;
  }
  .card--front { top: 111px; }
  .card--back { top: 640px; }
  .card__surface {
    position: absolute; inset: 0;
    background: linear-gradient(135deg, var(--card-light) 0%, var(--card-dark) 50%, var(--card-light) 100%);
  }

  .wordmark {
    position: absolute; left: 0; right: 0; top: 190px;
    display: flex; justify-content: center; align-items: center; gap: 14px;
    color: var(--white); font-size: 34px; font-weight: 400; letter-spacing: 6px;
  }
  .wordmark__square { width: 22px; height: 22px; background: var(--white); }

  .identity { position: absolute; color: var(--white); text-align: center; }
  .identity__name { font-weight: 400; text-transform: uppercase; line-height: 1; white-space: nowrap; }
  .identity__role {
    display: flex; align-items: center; gap: 6px;
    text-transform: uppercase; white-space: nowrap; color: var(--soft-white);
  }
  .identity__role::before, .identity__role::after {
    content: ""; flex: 1; height: 1.5px; background: var(--soft-white);
  }
  .card--front .identity { left: 0; right: 0; top: 278px; display: flex; flex-direction: column; align-items: center; }
  .card--front .identity__name { font-size: 43px; }
  .card--front .identity__role { width: 376px; margin-top: 6px; font-size: 16px; letter-spacing: 4px; }
  .card--back .identity { left: 385px; top: 148px; width: 290px; }
  .card--back .identity__name { font-size: 33px; }
  .card--back .identity__role { margin-top: 4px; font-size: 13px; letter-spacing: 3px; }

  .portrait {
    position: absolute; left: 41px; top: 52px; width: 305px; height: 435px;
    background: linear-gradient(180deg, var(--photo-mid) 0%, var(--photo-dark) 100%);
    border-radius: 120px 120px 0 0;
  }

  .contacts { position: absolute; left: 385px; top: 251px; color: var(--soft-white); list-style: none; }
  .contacts__item { display: flex; align-items: center; gap: 12px; font-size: 20px; height: 26px; }
  .contacts__icon { width: 16px; height: 16px; fill: var(--accent); }
  .website {
    position: absolute; left: 385px; top: 322px;
    font-size: 19px; font-style: italic; font-weight: 700; letter-spacing: 1px; color: var(--white);
  }
  .website__name { color: var(--accent); }
</style>
</head>
<body>
  <section class="card card--front">
    <div class="card__surface" role="img" aria-label="Dark grey geometric background pattern"></div>
    <div class="wordmark"><span class="wordmark__square"></span>LENDHART</div>
    <div class="identity">
      <h1 class="identity__name">Tobias Lendhart</h1>
      <p class="identity__role">Personal Trainer</p>
    </div>
  </section>

  <section class="card card--back">
    <div class="card__surface" role="img" aria-label="Dark grey geometric background pattern"></div>
    <div class="portrait" role="img" aria-label="Black and white portrait photo of the trainer, arms crossed"></div>
    <div class="identity">
      <h2 class="identity__name">Tobias Lendhart</h2>
      <p class="identity__role">Personal Trainer</p>
    </div>
    <ul class="contacts">
      <li class="contacts__item">
        <svg class="contacts__icon" viewBox="0 0 16 16" aria-hidden="true"><path d="M4 1 6 5 4.5 6.5c.8 2 2.5 3.9 4.5 5L10.5 10l4 2-1 3C8 15 1.5 8.5 1 2.5z"/></svg>
        0162/3819204
      </li>
      <li class="contacts__item">
        <svg class="contacts__icon" viewBox="0 0 16 16" aria-hidden="true"><path d="M1 3h14v10H1zM2.5 4.5 8 9l5.5-4.5z" fill-rule="evenodd"/></svg>
        hallo@lendhart-coaching.de
      </li>
    </ul>
    <p class="website">www.<span class="website__name">LENDHART-COACHING</span>.de</p>
  </section>
</body>
</html>
```